Desktop and Mobile Home Page Redesign

Please tailor the attached wireframe i made with your own design.
The key is to have the social icons being prominent, then have effectively 3 rows of mis-leveled posts to track the eye down the page.
At the bottom, I would like for you to design the same post types that dailyvortle.com.au have (attached) - I did not have time to add it into the wire frame.
Please design your own elements rather than taking from other sites direct.
Check out pelinora.com.au
We need a home page design for mobile and desktop (adaptive)
Must have features (desktop)
- Call to action buttons (large and attractive eg "Get More")
- The new redesign must be familiar to the old
- The design must have elements that prompt the user to scroll down e.g the video tab on the left of http://quorbit.com.au/ which forces the eye down
- Must have image galleries incorporated on the home page
-Must have room for 2 350x250 banners, 2 160x600 banners and 2 728x90 banners
- Must have originally formatted content in the middle of the page that would encourage navigation DEEP into the site (e.g think about how to format posts, polls, sliders, lists, galleries, videos, categories and menus, star rating)
- Must keep footer
- Must be adaptive
- Must have large and prominent share icons for each article and piece of content
- Must have a way to easily view comments
Must have features (mobile)
- Adaptive to zentrix and vaLphone
- Adaptive to both horizontal and vertical
- Easy tapping ability (finger size)
-Must have room for mobile banners
Updates
Target Market(s)
Females
Industry/Entity Type
Tailor
Requirements
Must have
- Check out pelinora.com.au
- Hero post
- Must keep footer
- Must be adaptive

```html
<!DOCTYPE html>
<html lang="en">
<head>
<meta charset="utf-8">
<title>Pelinora – Home</title>
<link href="https://fonts.googleapis.com/css2?family=Open+Sans:ital,wdth,wght@0,75..100,300..800;1,100,400&display=swap" rel="stylesheet">
<style>
:root{
  --ink:#222;
  --muted:#777;
  --line:#d8d8d8;
  --navy:#2b4a7a;
  --blue:#1f66c1;
  --sky:#3fb0e6;
  --red:#d71920;
  --green:#3aa655;
  --orange:#f37021;
  --yellow:#f6c400;
  --crimson:#b3163d;
  --pink:#ef5a8f;
  --magenta:#a23c8c;
  --coral:#f04a4a;
  --caption:rgba(45,45,45,.8);
  --footer:#3a3a3a;
  --footer-deep:#2c2c2c;
  --like:#4a64a8;
  --chirp:#3aa6d8;
}
*{box-sizing:border-box;margin:0;padding:0}
html,body{width:1200px;height:3377px;overflow:hidden}
body{position:relative;background:#fff;font-family:"Open Sans",Arial,sans-serif;color:var(--ink);font-size:13px}
.abs{position:absolute}
a{color:inherit;text-decoration:none}

/* header */
.brand{left:32px;top:18px}
.brand-name{font-size:50px;font-weight:800;letter-spacing:1px;line-height:54px}
.brand-tag{font-size:17px;margin-top:2px}
.account{left:640px;top:24px;font-size:12px;color:#555}
.account span{margin:0 6px;color:#aaa}
.search{left:822px;top:20px;display:flex}
.search input{width:272px;height:26px;border:1px solid #bbb;font:italic 12px "Open Sans",sans-serif;padding:0 8px;color:#999}
.search button{width:70px;height:26px;border:0;background:var(--navy);color:#fff;font:600 12px "Open Sans",sans-serif;margin-left:2px}
.cta{left:878px;top:66px;width:282px;height:48px;background:var(--navy);color:#fff;font:600 19px "Open Sans",sans-serif;display:flex;align-items:center;justify-content:center;gap:14px;clip-path:polygon(0 12%,100% 0,100% 100%,4% 100%)}

/* nav */
.nav{left:11px;top:124px;width:1155px;height:42px;display:flex}
.nav a{height:38px;display:flex;align-items:center;justify-content:center;color:#fff;font-weight:700;font-size:19px;font-stretch:82%;letter-spacing:.3px;clip-path:polygon(0 8%,100% 0,97% 100%,0 96%)}
.nav .home{width:76px;background:var(--sky)}
.nav .news{width:85px;background:var(--blue)}
.nav .style{width:92px;background:#1e8fd6}
.nav .social{width:106px;background:var(--red)}
.nav .rel{width:195px;background:var(--green)}
.nav .ent{width:198px;background:var(--orange)}
.nav .par{width:162px;background:var(--yellow)}
.nav .food{width:90px;background:var(--crimson)}
.nav .well{width:151px;background:var(--pink)}
.subnav{left:11px;top:172px;width:1155px;display:flex;justify-content:space-around;font-size:10.5px;color:#a5a5a5;letter-spacing:.3px}

/* share buttons */
.share{display:flex;gap:5px;align-items:center}
.share .btn{display:inline-flex;align-items:center;gap:5px;height:21px;padding:0 8px;border-radius:3px;color:#fff;font-weight:700;font-size:11.5px}
.share .btn::before{content:"";width:9px;height:9px;background:rgba(255,255,255,.85);border-radius:2px}
.share .like{background:var(--like)}
.share .chirp{background:var(--chirp)}
.share .count{border:1px solid #bbb;background:#fff;color:#333;padding:0 6px;height:21px;display:inline-flex;align-items:center;font-size:11px;border-radius:2px}
.share .comments{background:#f2f2f2;font-weight:600}

.more-btn{position:absolute;right:0;bottom:0;background:var(--red);color:#fff;font-weight:700;font-size:12px;padding:7px 11px}
.photo{position:absolute;inset:0}

.post{position:absolute;overflow:hidden;box-shadow:0 0 0 2px #cfcfcf,0 2px 6px rgba(0,0,0,.25);background:#777}
.post .cap{position:absolute;left:0;right:0;bottom:0;background:var(--caption);color:#fff;padding:5px 8px 7px}
.post .cap h3{font-size:12.5px;font-weight:600}
.post .cap p{font-size:11px;line-height:14px;margin:1px 0 5px;padding-right:90px}

/* left column */
.side-card{position:absolute;left:11px;width:209px;background:#fff;box-shadow:0 1px 5px rgba(0,0,0,.25)}
.side-card .tag{height:34px;display:flex;align-items:center;padding-left:18px;color:#fff;font-weight:700;font-size:15px;width:215px;clip-path:polygon(0 0,100% 0,96% 100%,0 100%)}
.side-card .pic{position:relative;height:140px;margin:6px 0 0}
.side-card p{font-size:11px;color:#666;line-height:14px;padding:8px 12px 6px}
.side-card .share{padding:0 10px 12px;gap:4px}
.side-card .share .btn{padding:0 6px}

.talking{left:248px;top:581px;width:342px;height:31px;background:var(--yellow);color:#222;font-weight:800;font-size:15.5px;display:flex;align-items:center;padding-left:16px;clip-path:polygon(0 0,100% 0,97% 100%,0 100%)}

/* right column */
.weather{left:842px;top:193px;width:336px;height:154px;border:3px solid var(--navy);border-radius:8px;background:linear-gradient(#f4f8ff,#dfe9fb);overflow:hidden}
.weather .loc{position:absolute;left:78px;top:8px;font-size:13px;font-weight:700}
.weather .temp{position:absolute;left:86px;top:34px;font-size:46px;font-weight:300;color:#333}
.weather .fc{position:absolute;right:10px;top:26px;width:110px;height:78px;background:#fff;border:1px solid #9cb3dc;border-radius:4px;font-size:10px;font-weight:700;padding:4px 6px}
.weather .obs{position:absolute;left:78px;top:100px;font-size:9.5px;color:#333}
.weather .bar{position:absolute;left:0;right:0;bottom:0;height:22px;background:var(--navy);display:flex;justify-content:space-around;align-items:center;color:#fff;font-size:9.5px;font-weight:700}
.gauge{position:absolute;left:10px;top:10px}

.ad{left:826px;top:360px;width:351px;height:297px;background:linear-gradient(#f6fbf3,#dcefd7);border:1px solid #cfe3c8}
.ad .product{position:absolute;left:80px;top:16px;width:190px;height:150px;border-radius:6px}
.ad .name{position:absolute;left:0;right:0;top:172px;text-align:center;font-size:34px;font-weight:700;color:var(--green)}
.ad .line{position:absolute;left:0;right:0;top:222px;text-align:center;font-size:11.5px;color:var(--green);font-weight:600}
.ad .voucher{position:absolute;left:66px;top:245px;width:220px;height:36px;background:var(--green);color:#fff;font-weight:700;font-size:15px;display:flex;align-items:center;justify-content:center;border-radius:2px}

.video-title{left:832px;top:668px;width:340px;font-size:14px;font-weight:700;line-height:19px}
.player{left:832px;top:722px;width:334px;height:188px;background:#1d1d1d;border:3px solid #111}
.player .frame{position:absolute;left:0;right:0;top:0;height:158px}
.player .controls{position:absolute;left:0;right:0;bottom:0;height:24px;background:#111;display:flex;align-items:center;padding:0 8px;gap:8px}
.player .track{flex:1;height:4px;background:#555}
.video-links{left:840px;top:935px;width:330px;display:flex;justify-content:space-between;font-size:14px;font-weight:600;padding-right:20px}

.signup{left:826px;top:990px;width:351px;height:112px;background:#f2f2f2;border-top:1px solid var(--line)}
.signup h4{font-size:11.5px;color:#777;font-weight:600;padding:10px 14px 8px}
.signup .row{display:flex;gap:10px;padding:0 22px}
.signup input{width:186px;height:27px;border:1px solid #ccc;font:10.5px "Open Sans",sans-serif;padding:0 8px;color:#888}
.signup button{width:110px;height:27px;border:0;background:var(--blue);color:#fff;font:600 13px "Open Sans",sans-serif;border-radius:2px}
.signup .fan{display:flex;gap:6px;align-items:center;padding:9px 14px 0;font-size:11px;color:#555;line-height:13px}

.follow{left:826px;top:1103px;width:351px;height:30px;background:#6b6b6b;display:flex;align-items:center;gap:6px;padding:0 10px;color:#fff;font-size:11px}
.follow b{font-size:15px;margin-right:4px}
.follow i{display:inline-block;width:18px;height:18px;border-radius:3px}

.fbox{left:826px;top:1142px;width:351px;height:264px;border:1px solid #bbb;background:#fff}
.fbox .head{background:#eef0f5;padding:6px 10px;font-size:12.5px;font-weight:700;border-bottom:1px solid #ccd}
.fbox .num{font-size:11px;padding:7px 12px;color:#333}
.fbox .fans{display:grid;grid-template-columns:repeat(5,58px);gap:8px;padding:0 12px}
.fbox .fan{font-size:9px;text-align:center;color:#555}
.fbox .fan span{display:block;height:54px;margin-bottom:3px}
.fbox .plugin{position:absolute;left:10px;bottom:6px;font-size:10px;color:#5c6fa3}

.galleries{left:832px;top:1416px;width:345px}
.galleries h4{font-size:15px;font-weight:700;margin-bottom:10px}
.gal-grid{display:grid;grid-template-columns:repeat(3,104px);gap:16px}
.gal-grid figure span{display:block;height:112px;border:1px solid #ccc}
.gal-grid figcaption{font-size:9.5px;color:#666;line-height:13px;margin-top:6px}

/* sections */
.sec-head{left:8px;width:1180px;border-bottom:2px solid var(--line)}
.sec-head span{display:flex;align-items:center;width:345px;height:34px;color:#fff;font-weight:700;font-size:19px;padding-left:12px;clip-path:polygon(0 0,100% 0,97% 100%,0 100%)}
.item{left:603px;width:580px}
.item h4{font-size:15px;font-weight:600;color:#333;margin-bottom:8px;letter-spacing:.2px}
.item .body{display:flex;gap:12px}
.item .thumb{width:165px;height:100px;flex:none;position:relative;box-shadow:0 0 0 1px #ccc}
.item p{font-size:12px;line-height:16px;color:#444}
.item .share{margin-top:8px}
.more-link{font-size:14px;font-weight:600;color:var(--red)}

/* footer */
.footer{left:0;top:3071px;width:1200px;height:248px;background:var(--footer)}
.footer ul{position:absolute;top:26px;list-style:none;font-size:12px;line-height:21px;color:#e2e2e2}
.legal{left:0;top:3319px;width:1200px;height:58px;background:var(--footer-deep);border-top:1px solid #555}
.legal .icons{position:absolute;left:78px;top:17px;display:flex;gap:8px}
.legal .icons i{width:24px;height:24px;border-radius:3px;display:block}
.legal .copy{position:absolute;right:20px;top:20px;color:#bbb;font-size:12px}
</style>
</head>
<body>

<header>
  <div class="abs brand">
    <div class="brand-name">PELINORA</div>
    <div class="brand-tag">What everyone's talking about</div>
  </div>
  <div class="abs account">REGISTER<span>|</span>SIGN IN</div>
  <form class="abs search"><input value="type your word here"><button type="button">SEARCH</button></form>
  <a class="abs cta" href="#"><svg width="18" height="18" viewBox="0 0 18 18"><rect x="2" y="2" width="14" height="14" fill="none" stroke="#fff" stroke-width="2"/><path d="M6 9h6M9 6l3 3-3 3" stroke="#fff" stroke-width="2" fill="none"/></svg>CALL TO ACTION</a>
</header>

<nav class="abs nav">
  <a class="home">HOME</a><a class="news">NEWS</a><a class="style">STYLE</a><a class="social">SOCIAL</a><a class="rel">RELATIONSHIPS</a><a class="ent">ENTERTAINMENT</a><a class="par">PARENTING</a><a class="food">FOOD</a><a class="well">WELLBEING</a>
</nav>
<div class="abs subnav"><span>PRODUCT REVIEWS</span><span>TRAVEL</span><span>GALLERIES</span><span>VIDEOS</span><span>PELINORA CARES</span><span>ABOUT</span><span>ADVERTISE</span><span>CONTACT</span></div>

<!-- hero row -->
<article class="post" style="left:11px;top:198px;width:456px;height:358px">
  <div class="photo" role="img" aria-label="Family portrait of parents and two children in front of a white house and garden" style="background:radial-gradient(ellipse 35% 45% at 45% 55%,#d9a98a,transparent 70%),radial-gradient(ellipse 30% 50% at 70% 45%,#e6c4a8,transparent 70%),radial-gradient(ellipse 40% 60% at 90% 30%,#5d7a3e,transparent 75%),linear-gradient(90deg,#e9ece8 0,#c8cfc9 25%,#6c8a4e 70%,#3f5a2c 100%)"></div>
  <div class="cap"><h3>Eye Grabbing, Jaw Dropping Title!</h3><p>Nunc varius facilisis eros. Sed erat. In in velit quis arcu ornare laoreet. Nunc sis eros. Sed erat. In in velit quis arcu ornare laoreet.</p>
  <div class="share"><span class="btn like">Like</span><span class="count">3k</span><span class="btn chirp">Chirp</span><span class="count">316</span><span class="count comments">Comments</span><span class="count">16</span></div></div>
  <a class="more-btn">Read More &gt;&gt;</a>
</article>
<article class="post" style="left:480px;top:198px;width:320px;height:170px">
  <div class="photo" role="img" aria-label="Celebrity with blonde hair in sunglasses at an event" style="background:radial-gradient(ellipse 35% 60% at 55% 35%,#e8d3a6,transparent 70%),radial-gradient(ellipse 25% 40% at 15% 40%,#b39a86,transparent 70%),linear-gradient(135deg,#4a4440,#2a2624)"></div>
  <div class="cap"><h3>Crazy News</h3><p>Nunc varius facilisis eros. Sed erat. In in velit quis arcu ornare laoreet. Nunc sis eros. Sed erat.</p>
  <div class="share"><span class="btn like">Like</span><span class="count">3k</span><span class="btn chirp">Chirp</span><span class="count">316</span></div></div>
  <a class="more-btn">More &gt;&gt;</a>
</article>
<article class="post" style="left:480px;top:382px;width:320px;height:174px">
  <div class="photo" role="img" aria-label="Crowd of photographers and fans at a premiere" style="background:radial-gradient(ellipse 20% 40% at 55% 35%,#cfb6a0,transparent 70%),radial-gradient(ellipse 50% 30% at 30% 30%,#7c7670,transparent 70%),radial-gradient(ellipse 40% 30% at 80% 25%,#8a8580,transparent 70%),linear-gradient(#3a3a3a,#1a1a1a)"></div>
  <div class="cap"><h3>Provocative</h3><p>Nunc varius facilisis eros. Sed erat. In in velit quis arcu ornare laoreet. Nunc sis eros. Sed erat.</p>
  <div class="share"><span class="btn like">Like</span><span class="count">3k</span><span class="btn chirp">Chirp</span><span class="count">316</span><span class="count">16</span></div></div>
  <a class="more-btn">More &gt;&gt;</a>
</article>

<!-- left category column -->
<aside>
  <div class="side-card" style="top:574px">
    <div class="tag" style="background:var(--sky)">Social</div>
    <div class="pic" role="img" aria-label="Portrait of a woman with long brown hair" style="background:radial-gradient(ellipse 35% 45% at 50% 50%,#e2c2ad,transparent 75%),linear-gradient(90deg,#5a3f32,#8c6a58 50%,#5a3f32)"></div>
    <p>Why this man needs to dye his hair</p>
    <div class="share"><span class="btn like">Like</span><span class="count">3k</span><span class="btn chirp">Chirp</span><span class="count">316</span></div>
  </div>
  <div class="side-card" style="top:855px">
    <div class="tag" style="background:var(--magenta)">Parenting</div>
    <div class="pic" role="img" aria-label="Mother and young child smiling together" style="background:radial-gradient(ellipse 25% 40% at 35% 40%,#dcb8a0,transparent 75%),radial-gradient(ellipse 22% 35% at 70% 60%,#e6c8b2,transparent 75%),linear-gradient(#d4d0c8,#a89a8a)"></div>
    <p>Why this man needs to dye his hair</p>
    <div class="share"><span class="btn like">Like</span><span class="count">3k</span><span class="btn chirp">Chirp</span><span class="count">316</span></div>
  </div>
  <div class="side-card" style="top:1125px">
    <div class="tag" style="background:var(--pink)">Body Image</div>
    <div class="pic" role="img" aria-label="Woman with flowing hair in warm golden light" style="background:radial-gradient(ellipse 40% 55% at 45% 50%,#c98a5a,transparent 75%),linear-gradient(90deg,#f0e6d6,#7a4a2a 45%,#3d2616)"></div>
    <p>Why this man needs to dye his hair</p>
    <div class="share"><span class="btn like">Like</span><span class="count">3k</span><span class="btn chirp">Chirp</span><span class="count">316</span></div>
  </div>
  <div class="side-card" style="top:1406px">
    <div class="tag" style="background:var(--coral)">News</div>
    <div class="pic" role="img" aria-label="Woman with purple hair in front of a campaign board" style="background:radial-gradient(ellipse 30% 40% at 60% 30%,#8d5aa8,transparent 75%),radial-gradient(ellipse 28% 40% at 60% 70%,#efd3c2,transparent 75%),linear-gradient(#f2f2f2,#d6d6d6)"></div>
    <p>Why this man needs to dye his hair</p>
    <div class="share"><span class="btn like">Like</span><span class="count">3k</span><span class="btn chirp">Chirp</span><span class="count">316</span></div>
  </div>
</aside>

<!-- centre feed -->
<div class="abs talking">TODAY WE'RE TALKING ABOUT:</div>
<main>
  <article class="post" style="left:252px;top:621px;width:536px;height:213px">
    <div class="photo" role="img" aria-label="Man in dark sunglasses at a television event" style="background:radial-gradient(ellipse 30% 55% at 40% 40%,#c9a68a,transparent 70%),radial-gradient(ellipse 20% 40% at 88% 45%,#b08a70,transparent 70%),linear-gradient(90deg,#d8d4cf,#7a6a5e 50%,#3a322c)"></div>
    <div class="cap"><h3>Outrageous Info</h3><p>Nunc varius facilisis eros. Sed erat. In in velit quis arcu ornare laoreet. Nunc sis eros. Sed erat.</p><div class="share"><span class="btn like">Like</span><span class="count">3k</span><span class="btn chirp">Chirp</span><span class="count">316</span><span class="count comments">Comments</span><span class="count">16</span></div></div>
    <a class="more-btn">Read More &gt;&gt;</a>
  </article>
  <article class="post" style="left:252px;top:851px;width:536px;height:213px">
    <div class="photo" role="img" aria-label="Two side-by-side photos of women at public events" style="background:radial-gradient(ellipse 18% 35% at 25% 35%,#d8b49c,transparent 75%),radial-gradient(ellipse 18% 35% at 75% 30%,#e2c0a6,transparent 75%),linear-gradient(90deg,#5a4c44,#8e7e72 48%,#e9e5e0 50%,#6a5a52 80%,#2c2624)"></div>
    <div class="cap"><h3>Hilarious Commentary</h3><p>Nunc varius facilisis eros. Sed erat. In in velit quis arcu ornare laoreet. Nunc sis eros. Sed erat.</p><div class="share"><span class="btn like">Like</span><span class="count">3k</span><span class="btn chirp">Chirp</span><span class="count">316</span><span class="count comments">Comments</span><span class="count">16</span></div></div>
    <a class="more-btn">Read More &gt;&gt;</a>
  </article>
  <article class="post" style="left:252px;top:1081px;width:536px;height:213px">
    <div class="photo" role="img" aria-label="Man in a grey hooded top and sunglasses against a blue sky" style="background:radial-gradient(ellipse 28% 60% at 52% 55%,#9a9a9e,transparent 70%),radial-gradient(ellipse 14% 30% at 20% 55%,#d2d6da,transparent 70%),linear-gradient(#3f88c5,#7ab0da 60%,#4a6f96)"></div>
    <div class="cap"><h3>Interesting Gossip</h3><p>Nunc varius facilisis eros. Sed erat. In in velit quis arcu ornare laoreet. Nunc sis eros. Sed erat.</p><div class="share"><span class="btn like">Like</span><span class="count">3k</span><span class="btn chirp">Chirp</span><span class="count">316</span><span class="count comments">Comments</span><span class="count">16</span></div></div>
    <a class="more-btn">Read More &gt;&gt;</a>
  </article>
  <article class="post" style="left:252px;top:1311px;width:536px;height:213px">
    <div class="photo" role="img" aria-label="Audience seated in a wood-panelled meeting hall" style="background:radial-gradient(ellipse 60% 35% at 50% 70%,#8a5a44,transparent 75%),radial-gradient(ellipse 15% 30% at 85% 55%,#c94a3a,transparent 75%),linear-gradient(#e4d2b4,#c4a47e 45%,#7a5c44)"></div>
    <div class="cap"><h3>Interesting Gossip</h3><p>Nunc varius facilisis eros. Sed erat. In in velit quis arcu ornare laoreet. Nunc sis eros. Sed erat.</p><div class="share"><span class="btn like">Like</span><span class="count">3k</span><span class="btn chirp">Chirp</span><span class="count">316</span><span class="count comments">Comments</span><span class="count">16</span></div></div>
    <a class="more-btn">Read More &gt;&gt;</a>
  </article>
  <article class="post" style="left:252px;top:1542px;width:536px;height:213px">
    <div class="photo" role="img" aria-label="Person touching a glowing digital screen" style="background:radial-gradient(ellipse 40% 30% at 50% 30%,#c8dcf4,transparent 70%),radial-gradient(ellipse 25% 40% at 30% 65%,#5a7fb8,transparent 75%),linear-gradient(135deg,#1c2a4a,#3a5a8e 50%,#1c2a4a)"></div>
    <div class="cap"><h3>Interesting Gossip</h3><p>Nunc varius facilisis eros. Sed erat. In in velit quis arcu ornare laoreet. Nunc sis eros. Sed erat.</p><div class="share"><span class="btn like">Like</span><span class="count">3k</span><span class="btn chirp">Chirp</span><span class="count">316</span><span class="count comments">Comments</span><span class="count">16</span></div></div>
    <a class="more-btn">Read More &gt;&gt;</a>
  </article>
  <article class="post" style="left:252px;top:1773px;width:536px;height:213px">
    <div class="photo" role="img" aria-label="Smiling woman in front of a wall of coloured sticky notes" style="background:radial-gradient(ellipse 28% 55% at 38% 50%,#d8b096,transparent 75%),radial-gradient(ellipse 25% 40% at 80% 30%,#e8e48a,transparent 75%),radial-gradient(ellipse 20% 30% at 70% 70%,#8fd0c8,transparent 75%),linear-gradient(90deg,#5a3f30,#a88a74 40%,#e6e2c8)"></div>
    <div class="cap"><h3>Outrageous Info</h3><p>Nunc varius facilisis eros. Sed erat. In in velit quis arcu ornare laoreet. Nunc sis eros. Sed erat.</p><div class="share"><span class="btn like">Like</span><span class="count">3k</span><span class="btn chirp">Chirp</span><span class="count">316</span><span class="count comments">Comments</span><span class="count">16</span></div></div>
    <a class="more-btn">Read More &gt;&gt;</a>
  </article>
  <article class="post" style="left:252px;top:2003px;width:536px;height:213px">
    <div class="photo" role="img" aria-label="Woman in a dimly lit office" style="background:radial-gradient(ellipse 22% 45% at 55% 45%,#b89480,transparent 75%),radial-gradient(ellipse 40% 40% at 20% 40%,#6a625c,transparent 75%),linear-gradient(135deg,#3a3633,#2a2725)"></div>
    <div class="cap"><h3>Hilarious Commentary</h3><p>Nunc varius facilisis eros. Sed erat. In in velit quis arcu ornare laoreet. Nunc sis eros. Sed erat.</p><div class="share"><span class="btn like">Like</span><span class="count">3k</span><span class="btn chirp">Chirp</span><span class="count">316</span><span class="count comments">Comments</span><span class="count">16</span></div></div>
    <a class="more-btn">Read More &gt;&gt;</a>
  </article>
</main>

<!-- right column -->
<aside>
  <div class="abs weather">
    <svg class="gauge" width="60" height="110" viewBox="0 0 60 110"><circle cx="30" cy="30" r="24" fill="#fff" stroke="#2b4a7a" stroke-width="3"/><path d="M30 30V12M30 30l10 8" stroke="#2b4a7a" stroke-width="3" stroke-linecap="round"/><rect x="24" y="58" width="12" height="44" rx="6" fill="#fff" stroke="#2b4a7a" stroke-width="2"/><rect x="27" y="72" width="6" height="28" rx="3" fill="#d71920"/></svg>
    <div class="loc">Larkfield, MD (20871)</div>
    <div class="temp">59°F</div>
    <div class="fc">WED's Forecast<br><span style="font-weight:400">Hi: 72°<br>Lo: 52°</span><br><span style="color:#d71920">ALERTS</span></div>
    <div class="obs">› More Observations</div>
    <div class="bar"><span>FORECAST</span><span>RADAR</span><span>LIVE CAMS</span><span>MORE</span></div>
  </div>

  <div class="abs ad">
    <div class="product" role="img" aria-label="Row of green disinfectant spray cans" style="background:linear-gradient(90deg,#2f8f3d,#8fd07a 10%,#2f8f3d 20%,#8fd07a 30%,#2f8f3d 40%,#8fd07a 50%,#2f8f3d 60%,#8fd07a 70%,#2f8f3d 80%,#8fd07a 90%,#2f8f3d)"></div>
    <div class="name">AIRELLA 20</div>
    <div class="line">ONE SPRAY. ONE HUNDRED AND ONE USES.</div>
    <div class="voucher">REDEEM YOUR VOUCHER</div>
  </div>

  <div class="abs video-title">Pelinora has a cup of Cuppa and a chat with Clara Bennett</div>
  <div class="abs player">
    <div class="frame" role="img" aria-label="Video still of a singer in a studio" style="background:radial-gradient(ellipse 30% 50% at 35% 50%,#d6b49c,transparent 75%),linear-gradient(90deg,#4a423c,#9a8c80 50%,#c8c0b6)"></div>
    <svg class="abs" style="left:129px;top:40px" width="70" height="70" viewBox="0 0 70 70"><circle cx="35" cy="35" r="32" fill="rgba(0,0,0,.45)" stroke="#fff" stroke-width="3"/><path d="M27 20l24 15-24 15z" fill="#fff"/></svg>
    <div class="controls"><svg width="10" height="12"><path d="M0 0l10 6-10 6z" fill="#ddd"/></svg><div class="track"></div><span style="color:#ccc;font-size:10px">0:00</span></div>
  </div>
  <div class="abs video-links"><span>› View full post</span><span>› More videos</span></div>

  <div class="abs signup">
    <h4>SIGN UP FOR PELINORA DAILY SENT TO YOUR INBOX</h4>
    <div class="row"><input value="Enter Your email"><button type="button">Get Updates</button></div>
    <div class="fan"><span class="share"><span class="btn like">Like</span></span><span>41,785 people like this. Be the first of your friends.</span></div>
  </div>
  <div class="abs follow"><b>follow us</b><i style="background:#4a64a8"></i><i style="background:#f7931e"></i><i style="background:#3aa6d8"></i><i style="background:#c0392b"></i><span>or become a member »</span></div>

  <div class="abs fbox">
    <div class="head">Find us on Friendsy</div>
    <div class="num">2,911 people like</div>
    <div class="fans">
      <div class="fan"><span role="img" aria-label="Member profile picture" style="background:linear-gradient(#7a8aa0,#c6a890)"></span>Oren</div>
      <div class="fan"><span role="img" aria-label="Member profile picture" style="background:linear-gradient(#e0c28e,#b0805a)"></span>Elin</div>
      <div class="fan"><span role="img" aria-label="Member profile picture" style="background:linear-gradient(#d0d0d0,#7a7a7a)"></span>Tamsin Cho</div>
      <div class="fan"><span role="img" aria-label="Member profile picture" style="background:linear-gradient(#c89a8c,#7a4a44)"></span>Lira</div>
      <div class="fan"><span role="img" aria-label="Member profile picture" style="background:linear-gradient(#9aa67a,#4a5a3a)"></span>Sefton Dal</div>
      <div class="fan"><span role="img" aria-label="Member profile picture" style="background:linear-gradient(#b8a08a,#6a5848)"></span>Hala</div>
      <div class="fan"><span role="img" aria-label="Member profile picture" style="background:linear-gradient(#8a9ab4,#3a4a64)"></span>Ayla</div>
      <div class="fan"><span role="img" aria-label="Member profile picture" style="background:linear-gradient(#e0ccb0,#a08870)"></span>Amir</div>
      <div class="fan"><span role="img" aria-label="Member profile picture" style="background:linear-gradient(#b8a0c8,#6a5a7c)"></span>Nolan</div>
      <div class="fan"><span role="img" aria-label="Member profile picture" style="background:linear-gradient(#c4bab0,#7a7068)"></span>Alcan</div>
    </div>
    <div class="plugin">Friendsy social plugin</div>
  </div>

  <section class="abs galleries">
    <h4>Photo Galleries</h4>
    <div class="gal-grid">
      <figure><span role="img" aria-label="Fashion week portrait" style="background:radial-gradient(ellipse 40% 45% at 50% 50%,#7a4a30,transparent 75%),linear-gradient(#1a1410,#5a3a2a)"></span><figcaption>Harbourside Style Week day 2 most</figcaption></figure>
      <figure><span role="img" aria-label="Fashion week portrait" style="background:radial-gradient(ellipse 40% 45% at 50% 50%,#e6c8a8,transparent 75%),linear-gradient(#c8a478,#8a6a48)"></span><figcaption>Harbourside Style Week day 2 most</figcaption></figure>
      <figure><span role="img" aria-label="Fashion week portrait" style="background:radial-gradient(ellipse 40% 45% at 50% 55%,#eccab8,transparent 75%),linear-gradient(#c23c3c,#e4a898)"></span><figcaption>Harbourside Style Week day 2 most</figcaption></figure>
      <figure><span role="img" aria-label="Fashion week portrait" style="background:radial-gradient(ellipse 40% 45% at 50% 50%,#e0c0a4,transparent 75%),linear-gradient(#6e7d5a,#3a4630)"></span><figcaption>Harbourside Style Week day 2 most</figcaption></figure>
      <figure><span role="img" aria-label="Fashion week portrait" style="background:radial-gradient(ellipse 40% 45% at 50% 55%,#e8c09a,transparent 75%),linear-gradient(#5a2e1a,#a86a40)"></span><figcaption>Harbourside Style Week day 2 most</figcaption></figure>
      <figure><span role="img" aria-label="Fashion week portrait" style="background:radial-gradient(ellipse 40% 45% at 50% 50%,#d8b49a,transparent 75%),linear-gradient(#a89888,#5a4c40)"></span><figcaption>Harbourside Style Week day 2 most</figcaption></figure>
    </div>
  </section>
</aside>

<!-- entertainment -->
<section>
  <div class="abs sec-head" style="top:2239px"><span style="background:var(--navy)">Entertainment</span></div>
  <article class="post" style="left:29px;top:2313px;width:530px;height:286px">
    <div class="photo" role="img" aria-label="Speaker presenting beside a red slide about design consistency" style="background:radial-gradient(ellipse 22% 40% at 18% 35%,#c89a80,transparent 75%),radial-gradient(ellipse 10% 15% at 62% 62%,#e05040,transparent 80%),radial-gradient(ellipse 10% 15% at 84% 62%,#f0e2b0,transparent 80%),linear-gradient(90deg,#2a2e3a,#3a3f4e 30%,#c83a48 40%,#e2707a)"></div>
    <div class="cap"><h3>Interesting Gossip</h3><p>Nunc varius facilisis eros. Sed erat. In in velit quis arcu ornare laoreet. Nunc sis eros. Sed erat.</p><div class="share"><span class="btn like">Like</span><span class="count">3k</span><span class="btn chirp">Chirp</span><span class="count">316</span><span class="count comments">Comments</span><span class="count">16</span></div></div>
    <a class="more-btn">More &gt;&gt;</a>
  </article>
  <div class="abs item" style="top:2316px">
    <h4>LORUM IPSUM DOLLAR</h4>
    <div class="body"><div class="thumb" role="img" aria-label="Couple at a red carpet event" style="background:radial-gradient(ellipse 25% 45% at 35% 40%,#d4b09a,transparent 75%),radial-gradient(ellipse 22% 45% at 70% 40%,#c8a08a,transparent 75%),linear-gradient(#8a8580,#2a2a2a)"></div>
    <div><p>Lorem ipsum dolor sit amet, consectetuer adipiscing elit. Lorem ipsum dolor sit amet, consectetuer adipiscing elit. Lorem ipsum dolor sit amet, consectetuer adipiscing elit.</p><div class="share"><span class="btn like">Like</span><span class="count">3k</span><span class="btn chirp">Chirp</span><span class="count">316</span></div></div></div>
  </div>
  <div class="abs item" style="top:2477px">
    <h4>LORUM IPSUM DOLLAR</h4>
    <div class="body"><div class="thumb" role="img" aria-label="Two women posing at an event" style="background:radial-gradient(ellipse 22% 45% at 30% 40%,#d8b6a0,transparent 75%),radial-gradient(ellipse 22% 45% at 72% 40%,#caa48c,transparent 75%),linear-gradient(#b0a69c,#3a3330)"></div>
    <div><p>Lorem ipsum dolor sit amet, consectetuer adipiscing elit. Lorem ipsum dolor sit amet, consectetuer adipiscing elit. Lorem ipsum dolor sit amet, consectetuer adipiscing elit.</p><div class="share"><span class="btn like">Like</span><span class="count">3k</span><span class="btn chirp">Chirp</span><span class="count">316</span></div></div></div>
  </div>
  <a class="abs more-link" style="left:1070px;top:2646px">More &gt;&gt;</a>
</section>

<!-- wellbeing -->
<section>
  <div class="abs sec-head" style="top:2666px"><span style="background:var(--pink)">WellBeing</span></div>
  <article class="post" style="left:29px;top:2734px;width:530px;height:288px">
    <div class="photo" role="img" aria-label="Group of smiling friends outdoors by a brick building" style="background:radial-gradient(ellipse 15% 25% at 25% 40%,#e0b89c,transparent 75%),radial-gradient(ellipse 15% 25% at 45% 30%,#d8ac90,transparent 75%),radial-gradient(ellipse 15% 25% at 70% 35%,#e4bea4,transparent 75%),radial-gradient(ellipse 30% 30% at 50% 80%,#3a5a8a,transparent 75%),linear-gradient(90deg,#7a5a44,#a4826a 50%,#d0c8bc)"></div>
    <div class="cap"><h3>Interesting Gossip</h3><p>Nunc varius facilisis eros. Sed erat. In in velit quis arcu ornare laoreet. Nunc sis eros. Sed erat.</p><div class="share"><span class="btn like">Like</span><span class="count">3k</span><span class="btn chirp">Chirp</span><span class="count">316</span><span class="count comments">Comments</span><span class="count">16</span></div></div>
    <a class="more-btn">More &gt;&gt;</a>
  </article>
  <div class="abs item" style="top:2738px">
    <h4>LORUM IPSUM DOLLAR</h4>
    <div class="body"><div class="thumb" role="img" aria-label="Family gathered on a sofa" style="background:radial-gradient(ellipse 40% 35% at 50% 45%,#d8b094,transparent 75%),linear-gradient(#a4826a,#5a4030)"></div>
    <div><p>Lorem ipsum dolor sit amet, consectetuer adipiscing elit. Lorem ipsum dolor sit amet, consectetuer adipiscing elit. Lorem ipsum dolor sit amet, consectetuer adipiscing elit.</p><div class="share"><span class="btn like">Like</span><span class="count">3k</span><span class="btn chirp">Chirp</span><span class="count">316</span></div></div></div>
  </div>
  <div class="abs item" style="top:2900px">
    <h4>LORUM IPSUM DOLLAR</h4>
    <div class="body"><div class="thumb" role="img" aria-label="People talking around a table" style="background:radial-gradient(ellipse 30% 35% at 40% 45%,#c8a48a,transparent 75%),linear-gradient(#8a7a6c,#3e342c)"></div>
    <div><p>Lorem ipsum dolor sit amet, consectetuer adipiscing elit. Lorem ipsum dolor sit amet, consectetuer adipiscing elit. Lorem ipsum dolor sit amet, consectetuer adipiscing elit.</p><div class="share"><span class="btn like">Like</span><span class="count">3k</span><span class="btn chirp">Chirp</span><span class="count">316</span></div></div></div>
  </div>
  <a class="abs more-link" style="left:1094px;top:3022px">More &gt;&gt;</a>
</section>

<footer>
  <div class="abs footer">
    <ul style="left:74px"><li>Home</li><li>Advertise with us</li><li>About</li><li>FAQs</li><li>Sitemap</li><li>Archives</li><li>Competitions &amp; Giveaways</li><li>Nora's Books</li><li>Privacy Policy</li><li>Contact us</li></ul>
    <ul style="left:281px"><li>Dating</li><li>Sex</li><li>Weddings &amp; Marriage</li><li>Gay and Lesbian</li><li>Breakups</li><li>Friendships</li><li>Family</li><li>Men</li><li>Women</li></ul>
    <ul style="left:484px"><li>Motherhood</li><li>Fatherhood</li><li>Pregnancy</li><li>Birth</li><li>Breastfeeding</li><li>Current Affairs</li><li>Media</li><li>Body Image and Retouching</li><li>Politics &amp; World</li></ul>
    <ul style="left:743px"><li>Career &amp; Money</li><li>Style</li><li>Fashion</li><li>Beauty</li><li>Lifestyle</li><li>Recipes</li><li>Nutrition</li><li>Wellbeing</li><li>Celebrity</li></ul>
    <ul style="left:990px"><li>Books</li><li>Movies</li><li>Technology and Gadgets</li><li>Social Media</li></ul>
  </div>
  <div class="abs legal">
    <div class="icons"><i style="background:#4a64a8"></i><i style="background:#3aa6d8"></i><i style="background:#f7931e"></i><i style="background:#1f77b4"></i></div>
    <div class="copy">© 2013 hollowfernstudio.com, All Rights Reserved</div>
  </div>
</footer>

</body>
</html>
```